Yoga Workshop - Yoga Practice information flyer

I am a yoga teacher who will be presenting a workshop on yoga for sleep and need a brochure for my clients which outlines a practice that I give them so they can do the practice at home. Ideally I would like a brochure that is a single A3 size of paper in size that folds in half to an A4 booklet with the entire practice on the centre section to make it easy for people to do the practice at home with just one open page in front of them:
* Front page detailing "Yoga for Sleep Workshop" and "Restorative Yoga Practice"
* Centre contains the information on the practice contained in the attached word document. The practice consists of 5 postures, so there needs to be five separate sections which have the pictures of the postures (attached in uploaded files) and the wording contained in the attached word document. All pictures uploaded need to be included in the flyer as each posture has different pictures demonstrating the posture using yoga props or using things people have at home
* Back page containing a picture of myself (picture uploaded in files) with some information about me (contained in the attached word document) and my website www.calmdrift.com.au

I also need this flyer to be able to printed on 2 double sided A4 sheets of paper so will require 2 x pdf file versions. Importantly, for the centre section of the flyer, the design needs to ensure if it is printed on A4 paper, the wording and pictures for each of the postures are not separated over two pages

Target Market(s)

Existing clients

Requirements
Must have
• Detailed in project description
Nice to have
• The word document also contains some quotes. These do not need to be included in the flyer. If there is room and there is room for one or two of those please include where it would look good
Should not have
• Stock pictures of people in yoga postures which a normal everyday person could not get into

```html
<!DOCTYPE html>
<html lang="en">
<head>
<meta charset="utf-8">
<title>Restorative Yoga Practice – Postures 3 to 5</title>
<link href="https://fonts.googleapis.com/css2?family=Josefin+Sans:ital,wght@0,400;0,700;1,300;1,400&display=swap" rel="stylesheet">
<style>
  :root {
    --rust: #a5371f;
    --navy: #34495e;
    --gold: #f7c52f;
    --cream: #ffffff;
    --wall: #e9e7e4;
    --floor: #6e3a1a;
    --mat: #1e8fc4;
    --shirt: #8c2a35;
  }
  * { margin: 0; padding: 0; box-sizing: border-box; }
  html, body { width: 848px; height: 1200px; overflow: hidden; }
  body {
    position: relative;
    font-family: "Josefin Sans", sans-serif;
    color: var(--cream);
    background: var(--rust);
  }
  .band { position: absolute; left: 0; width: 848px; }
  .band--rust { background: var(--rust); }
  .band--navy { background: var(--navy); }
  .band-top { top: 0; height: 349px; }
  .band-mid { top: 349px; height: 525px; }
  .band-bottom { top: 874px; height: 326px; }

  .photo {
    position: absolute;
    width: 169px;
    height: 260px;
    background: var(--cream);
    padding: 5px;
  }
  .photo-fill {
    width: 100%;
    height: 100%;
  }
  .photo-fill--wall-legs {
    background: linear-gradient(180deg, var(--wall) 0%, #d9d6d2 55%, #8a4a24 62%, var(--floor) 80%, #2a7fb0 100%);
  }
  .photo-fill--child {
    background: linear-gradient(180deg, var(--wall) 0%, #e3e1de 33%, #7a4220 36%, var(--floor) 55%, #8c3a2c 70%, var(--mat) 100%);
  }
  .photo-fill--supine {
    background: linear-gradient(180deg, var(--wall) 0%, #6f3b1c 7%, var(--floor) 40%, #4d6aa0 65%, #a55a2a 82%, var(--floor) 100%);
  }

  .posture-text { position: absolute; }
  .posture-title {
    font-weight: 700;
    color: var(--gold);
    font-size: 20px;
    line-height: 24px;
    letter-spacing: 0.4px;
  }
  .posture-copy {
    font-size: 14px;
    line-height: 15.7px;
    letter-spacing: 0.3px;
    margin-top: 15px;
  }
  .label {
    font-style: italic;
    font-weight: 300;
    color: var(--gold);
  }
</style>
</head>
<body>

  <section class="band band--rust band-top">
    <div class="photo" style="left:19px; top:43px;">
      <div class="photo-fill photo-fill--wall-legs" role="img" aria-label="Woman lying on a yoga mat with legs up the wall and a bolster under her hips, viewed from behind her head"></div>
    </div>
    <div class="photo" style="left:195px; top:43px;">
      <div class="photo-fill photo-fill--wall-legs" role="img" aria-label="Woman in legs-up-the-wall pose with a folded towel under her hips, arms resting out to the sides"></div>
    </div>
    <div class="posture-text" style="left:382px; top:26px; width:450px;">
      <h2 class="posture-title">Posture 3 - Elevated Legs-Up-the-Wall Pose</h2>
      <p class="posture-copy"><span class="label">Props</span> - 1 x bolsters (or towel or blanket densely folded to a<br>width of about 15-30cm), 1 x cushion for head support<br>(optional)</p>
      <p class="posture-copy"><span class="label">Set up notes</span> - To enter the posture sit at 90 degrees to the<br>wall with the side of your hip about a hand width away from<br>the wall, and the bolster/folded towel or blanket close by.&nbsp; Lie<br>down on the mat on your side then roll onto your back and<br>extend feet up wall.&nbsp; The feet can push into the wall to<br>elevate the hips slightly so the bolster/folded towel or blanket<br>can slide underneath the hips.&nbsp; The prop should be positioned<br>underneath the sacrum (flat bony structure at the base of<br>the spine).</p>
      <p class="posture-copy"><span class="label">Caution</span> - If any lower back pain is experience adjust the<br>height the hips are elevated by using a towel or blanket that<br>is folded to a lower height.</p>
    </div>
  </section>

  <section class="band band--navy band-mid">
    <div class="photo" style="left:42px; top:41px;">
      <div class="photo-fill photo-fill--child" role="img" aria-label="Supported child's pose seen from above, torso resting along a bolster on a blue mat"></div>
    </div>
    <div class="photo" style="left:290px; top:41px;">
      <div class="photo-fill photo-fill--child" role="img" aria-label="Supported child's pose from the side, head turned resting on a bolster"></div>
    </div>
    <div class="photo" style="left:543px; top:41px;">
      <div class="photo-fill photo-fill--child" role="img" aria-label="Supported child's pose with torso resting on a stack of bed pillows"></div>
    </div>
    <div class="posture-text" style="left:43px; top:328px; width:780px;">
      <h2 class="posture-title">Posture 4 - Supported Child’s Pose</h2>
      <p class="posture-copy" style="margin-top:12px;"><span class="label">Props</span> - 1-2 x bolsters (or 3-4 bed pillows)</p>
      <p class="posture-copy"><span class="label">Set up notes</span> - Position bolster or stacked pillows under torso.&nbsp; Rest the head in one direction and<br>remember to turn to the head to the other side half way through the time you spend in this posture.</p>
      <p class="posture-copy"><span class="label">Caution</span> - If any knee or hip pain is experience, increase the height of the support under the torso by<br>adding more bolsters, folded blankets or pillows.</p>
    </div>
  </section>

  <section class="band band--rust band-bottom">
    <div class="photo" style="left:19px; top:39px;">
      <div class="photo-fill photo-fill--supine" role="img" aria-label="Woman lying on her back on a mat in relaxation posture with a bolster under her knees"></div>
    </div>
    <div class="photo" style="left:195px; top:39px;">
      <div class="photo-fill photo-fill--supine" role="img" aria-label="Woman lying on her back in relaxation posture with a bed pillow under her knees"></div>
    </div>
    <div class="posture-text" style="left:382px; top:36px; width:450px;">
      <h2 class="posture-title">Posture 5 - Basic Relaxation Posture with<br>Knee Support</h2>
      <p class="posture-copy" style="margin-top:12px;"><span class="label">Props</span> - 1 x bolsters (or 1 x bed pillows or rolled up towel)</p>
      <p class="posture-copy"><span class="label">Set up notes</span> - Reclining on back, position bolster or pillows<br>under knees.</p>
    </div>
  </section>

</body>
</html>
```